Electrician Letterhead Design MVR

We need some letterhead for our bills and other papers.
Customer address is on the right side (Swiss format)
A4 format

Design should also be applicable on Cards

Target Market(s)

Private Customers, Small Business

Industry/Entity Type

Electrician

Other font styles liked:
• incised 901

Colors
00AB8E
00BBA5
67D7C9
C6EFE9
E9F9F6

```html
<!DOCTYPE html>
<html lang="en">
<head>
<meta charset="utf-8">
<title>MVR Letterhead</title>
<link rel="stylesheet" href="https://fonts.googleapis.com/css2?family=Exo+2:wght@700&family=Open+Sans:wght@400;600&display=swap">
<style>
  :root {
    --teal-deep: #00AB8E;
    --teal: #00BBA5;
    --teal-mid: #67D7C9;
    --teal-soft: #C6EFE9;
    --teal-mist: #E9F9F6;
    --paper: #ffffff;
    --backdrop: #e4e4e4;
    --ink: #4a4a4a;
    --wave-dark: #2f9e8e;
  }
  * { margin: 0; padding: 0; box-sizing: border-box; }
  html, body { width: 1200px; height: 800px; overflow: hidden; }
  body {
    background: var(--backdrop);
    font-family: "Open Sans", Arial, sans-serif;
    color: var(--ink);
    position: relative;
  }
  .letterhead {
    position: absolute;
    left: 336px;
    top: 18px;
    width: 528px;
    height: 764px;
    background: var(--paper);
    box-shadow: 0 6px 24px rgba(0,0,0,0.12);
    overflow: hidden;
  }
  .brand {
    position: absolute;
    left: 40px;
    top: 58px;
  }
  .brand-name {
    display: flex;
    align-items: center;
    gap: 8px;
    font-family: "Exo 2", Arial, sans-serif;
    font-weight: 700;
    font-size: 40px;
    line-height: 1;
    color: var(--teal-deep);
    letter-spacing: 1px;
  }
  .brand-dot {
    width: 12px; height: 12px;
    border-radius: 50%;
    background: var(--teal-deep);
  }
  .brand-tagline {
    margin-top: 4px;
    font-size: 9.5px;
    font-weight: 600;
    color: #333;
    letter-spacing: 0.3px;
  }
  .contact-list {
    position: absolute;
    right: 36px;
    top: 34px;
    list-style: none;
    font-size: 8.5px;
    line-height: 12px;
  }
  .contact-list li { display: flex; align-items: center; gap: 5px; }
  .contact-icon { width: 9px; height: 9px; flex: none; }
  .address {
    position: absolute;
    right: 36px;
    bottom: 118px;
    display: flex;
    gap: 6px;
    font-size: 9.5px;
    line-height: 13px;
  }
  .address-pin { width: 9px; height: 13px; flex: none; margin-top: 1px; }
  .footer-waves {
    position: absolute;
    left: 0; bottom: 0;
    width: 528px; height: 110px;
  }
</style>
</head>
<body>
  <main class="letterhead">
    <header class="brand">
      <div class="brand-name"><span>MVR</span><span class="brand-dot"></span></div>
      <div class="brand-tagline">Elektrotechnik Mavro GmbH</div>
    </header>

    <ul class="contact-list">
      <li><svg class="contact-icon" viewBox="0 0 10 10"><circle cx="5" cy="5" r="5" fill="var(--teal-deep)"/><path d="M3.3 2.6l1 1-.5.7a3 3 0 0 0 1.9 1.9l.7-.5 1 1-.6.8C5 7.2 2.8 5 2.5 3.2z" fill="#fff"/></svg>+01-2345-678900</li>
      <li><svg class="contact-icon" viewBox="0 0 10 10"><circle cx="5" cy="5" r="5" fill="var(--teal-deep)"/><path d="M3.3 2.6l1 1-.5.7a3 3 0 0 0 1.9 1.9l.7-.5 1 1-.6.8C5 7.2 2.8 5 2.5 3.2z" fill="#fff"/></svg>+01-2345-6789011</li>
      <li><svg class="contact-icon" viewBox="0 0 10 10"><circle cx="5" cy="5" r="5" fill="var(--teal-deep)"/><rect x="2.6" y="3.3" width="4.8" height="3.4" fill="none" stroke="#fff" stroke-width=".8"/><path d="M2.6 3.3L5 5.2l2.4-1.9" fill="none" stroke="#fff" stroke-width=".8"/></svg>info@mavro-elektro.com</li>
      <li><svg class="contact-icon" viewBox="0 0 10 10"><circle cx="5" cy="5" r="5" fill="var(--teal-deep)"/><circle cx="5" cy="5" r="2.5" fill="none" stroke="#fff" stroke-width=".7"/><path d="M2.5 5h5M5 2.5c-1.2 1.5-1.2 3.5 0 5M5 2.5c1.2 1.5 1.2 3.5 0 5" fill="none" stroke="#fff" stroke-width=".6"/></svg>www.mavro-elektro.com</li>
    </ul>

    <address class="address" style="font-style: normal;">
      <svg class="address-pin" viewBox="0 0 10 14"><path d="M5 1a4 4 0 0 0-4 4c0 3 4 8 4 8s4-5 4-8a4 4 0 0 0-4-4z" fill="none" stroke="var(--teal-deep)" stroke-width="1.2"/><circle cx="5" cy="5" r="1.4" fill="var(--teal-deep)"/></svg>
      <span>Suite 102 Street name, State,<br>Zip 2034, Country</span>
    </address>

    <svg class="footer-waves" viewBox="0 0 528 110" preserveAspectRatio="none" aria-hidden="true">
      <path d="M220 40 C300 10 360 0 420 8 C460 14 500 8 528 0 L528 110 L220 110 Z" fill="var(--teal-mid)"/>
      <path d="M0 52 C90 30 170 34 250 56 C330 78 420 66 528 40 L528 110 L0 110 Z" fill="var(--paper)"/>
      <path d="M0 62 C90 40 170 44 250 66 C330 88 430 76 528 50 L528 110 L0 110 Z" fill="var(--teal)"/>
      <path d="M0 78 C110 60 200 70 280 86 C360 100 450 96 528 80 L528 110 L0 110 Z" fill="var(--wave-dark)"/>
    </svg>
  </main>
</body>
</html>
```